Kestrel Finish Studio (KFS)

I would like to design a dedicated site for my KFS product, which allows industry employees to be trained in the visual inspection of mechanical parts. My product is a 3D simulator (see https://morvint-works.ch/our-applications/virtual-reality/ and https://morvint-works.ch for videos) which makes it possible to manufacture standard parts representative of a type of defect which is accepted or refused by the quality department. These master parts can be used to create a common quality culture in the company and to train employees in a homogeneous way. The simulator is initially designed for watchmaking, but must be designed for much broader industries (cars, phone reconditioning, ball bearings, etc.)
L'information que j'ai donnée n'est pas assez précise. Je dois préciser les domaines métiers visés par le site internet. J'ai besoin de quelques jours pour choisir les domaines les plus représentatifs.
Coded - Design and coding required
1 page

```html
<!DOCTYPE html>
<html lang="en">
<head>
<meta charset="utf-8">
<title>Kestrel Finish Studio</title>
<link rel="stylesheet" href="https://fonts.googleapis.com/css2?family=Roboto:wght@400;500;700;900&display=swap">
<style>
:root{
  --blue:#0b6fba;
  --blue-dark:#0a5f9f;
  --ink:#23252b;
  --text:#5b5f66;
  --navy:#1d2234;
  --white:#ffffff;
  --hero-dark:#06121a;
  --teal:#1fb7c4;
}
*{box-sizing:border-box;margin:0;padding:0}
html,body{width:1200px;height:4494px;overflow:hidden}
body{position:relative;background:var(--white);font-family:'Roboto',sans-serif;color:var(--ink)}
.abs{position:absolute}
.btn{position:absolute;display:flex;align-items:center;justify-content:center;background:var(--blue);color:var(--white);font-weight:700;border-radius:3px;text-decoration:none}

/* header */
.site-header{position:absolute;left:0;top:0;width:1200px;height:91px;background:var(--white);border-top:4px solid var(--blue)}
.brand{position:absolute;left:112px;top:20px;width:126px;text-align:center;color:var(--blue);font-weight:700;font-size:10.5px;line-height:12px;text-transform:uppercase}
.brand-mark{display:block;width:30px;height:18px;margin:0 auto 4px;background:var(--blue);border-radius:4px}
.nav{position:absolute;top:42px;left:447px}
.nav a{font-size:13px;font-weight:500;color:var(--ink);text-decoration:none;position:absolute;white-space:nowrap}
.nav-start{left:959px;top:31px;width:122px;height:35px;font-size:14px}

/* hero */
.hero{position:absolute;left:0;top:91px;width:1200px;height:552px;overflow:hidden;background:var(--hero-dark)}
.hero-art{position:absolute;left:0;top:0;width:560px;height:552px;background:radial-gradient(ellipse at 55% 45%,#1c8b96 0%,#0c3f4a 35%,#06121a 72%)}
.hero-title{position:absolute;right:112px;top:100px;text-align:right;color:var(--white);font-weight:900;font-size:78px;line-height:75px;letter-spacing:-1px}
.hero-btn{left:938px;top:359px;width:150px;height:44px;font-size:17px}
.dots{position:absolute;left:1052px;top:488px;display:flex;gap:6px}
.dots span{width:7px;height:7px;border-radius:50%;background:var(--white)}
.dots span.on{background:#4fb0ea}
.hero-curve{position:absolute;left:0;bottom:0}

/* about */
.section-title{font-weight:700;color:var(--ink);text-transform:uppercase}
.about-title{left:120px;top:760px;font-size:37px}
.body-copy{font-size:15px;line-height:23px;color:var(--text)}
.about-copy{left:120px;top:819px;width:455px}
.about-btn{left:120px;top:1074px;width:152px;height:44px;font-size:17px}
.blob{position:absolute;background:var(--blue)}
.blob-right{border-radius:0 40px 0 60px}
.blob-left{border-radius:60px 0 40px 0}
.framed{position:absolute;background:var(--white);padding:7px;box-shadow:0 2px 10px rgba(0,0,0,.22)}
.framed .fill{width:100%;height:100%}
.play{position:absolute;left:50%;top:50%;transform:translate(-50%,-50%)}

/* aesthetic control */
.control-band{position:absolute;left:0;top:1266px;width:1200px;height:508px;background:linear-gradient(180deg,#0c70bb,#0b66ad)}
.control-title{position:absolute;left:0;top:1314px;width:1200px;text-align:center;color:var(--white);font-weight:500;font-size:30px;text-transform:uppercase}
.card{position:absolute;width:309px;height:228px;background:var(--white);border-radius:4px;box-shadow:0 2px 8px rgba(0,0,0,.18);text-align:center}
.card svg{margin:40px auto 0;display:block}
.card p{margin:16px auto 0;width:258px;font-size:14.5px;line-height:20.5px;color:var(--text)}

/* feature rows */
.feature-title{font-size:38px;line-height:41px}
.feature-copy{width:455px}

/* allows */
.allows-shape{position:absolute;left:96px;top:3108px;width:1104px;height:471px;border-radius:236px 0 0 236px;background:linear-gradient(90deg,#0a63a8,#0b72bf 60%,#0b6fba)}
.allows-title{position:absolute;left:0;top:3182px;width:1296px;text-align:center;color:var(--white);font-weight:500;font-size:30px}
.allows-core{position:absolute;left:509px;top:3296px;width:213px;height:148px;background:var(--white);border-radius:4px;box-shadow:0 2px 10px rgba(0,0,0,.25);text-align:center;color:var(--blue);font-weight:700;font-size:13.5px;line-height:17px;padding-top:44px;text-transform:uppercase}
.allows-core .brand-mark{width:56px;height:24px;margin-bottom:8px}
.node{position:absolute;width:56px;height:56px;border-radius:50%;background:var(--white);box-shadow:0 0 0 5px rgba(255,255,255,.25);display:flex;align-items:center;justify-content:center}
.allows-text{position:absolute;width:260px;color:var(--white);font-size:14.5px;line-height:21.5px}
.allows-text.left{text-align:right}

/* accordion */
.acc-open{position:absolute;left:609px;top:3715px;width:479px;height:200px;background:var(--white);box-shadow:0 2px 10px rgba(0,0,0,.14);padding:30px 26px}
.acc-open h3{font-size:17px;font-weight:500;color:var(--ink);display:flex;justify-content:space-between}
.acc-open p{margin-top:14px;font-size:13px;line-height:20px;color:var(--text);width:400px}
.acc-bar{position:absolute;left:609px;width:479px;height:48px;background:var(--blue);color:var(--white);font-weight:700;font-size:17px;display:flex;align-items:center;justify-content:space-between;padding:0 24px 0 26px;border-radius:2px}

/* footer */
.site-footer{position:absolute;left:0;top:4203px;width:1200px;height:291px;background:var(--navy);color:var(--white)}
.footer-col{position:absolute;top:52px}
.footer-col h4{font-size:25px;font-weight:500;text-transform:uppercase;margin-bottom:14px}
.footer-col ul{list-style:none}
.footer-col li{font-size:13px;line-height:22px}
.contact li{display:flex;align-items:center;gap:12px}
.contact li .ico{width:14px;display:inline-flex;justify-content:center}
.copyright{position:absolute;left:0;top:256px;width:1200px;text-align:center;font-size:13px;color:#d9dbe3}
</style>
</head>
<body>

<header class="site-header">
  <div class="brand"><span class="brand-mark"></span>Kestrel Finish<br>Studio</div>
  <nav class="nav">
    <a style="left:0">SERVICES</a>
    <a style="left:101px">PARTNERS</a>
    <a style="left:206px">REFERENCES</a>
    <a style="left:327px">INFO</a>
    <a style="left:395px">CONTACT US</a>
  </nav>
  <a class="btn nav-start">Get Started</a>
</header>

<section class="hero">
  <div class="hero-art" role="img" aria-label="Glowing teal digital hand made of network lines touching a point of light"></div>
  <h1 class="hero-title">KESTREL<br>FINISH<br>STUDIO</h1>
  <a class="btn hero-btn">Get A Quote</a>
  <div class="dots"><span></span><span class="on"></span><span></span></div>
  <svg class="hero-curve" width="1200" height="60" viewBox="0 0 1200 60"><path d="M0 60 L0 40 Q600 -20 1200 12 L1200 60 Z" fill="#fff"/></svg>
</section>

<section class="about">
  <h2 class="abs section-title about-title">About KFS</h2>
  <p class="abs body-copy about-copy">It is a long established fact that a reader will be distracted by the readable content of a page when looking at its layout. The point of using Lorem Ipsum is that it has a more-or-less normal distribution of letters, as opposed to using 'Content here, content here', making it look like readable English. Many desktop publishing packages and web page editors now use Lorem Ipsum as their default model text, and a search for 'lorem ipsum' will uncover many web sites still in their infancy. Various versions have evolved over the years, sometimes by accident, sometimes on purpose (injected humour and the like).</p>
  <a class="btn about-btn">Read More</a>
  <div class="blob blob-right" style="left:978px;top:977px;width:154px;height:153px"></div>
  <div class="framed" style="left:624px;top:755px;width:464px;height:344px">
    <div class="fill" role="img" aria-label="Video still of a golden ring rendered in the 3D simulator beside a dark software panel" style="background:linear-gradient(90deg,#0e2f4a 0 17%,#0a0a0a 17%,#3a2a10 60%,#0b0b0b)"></div>
    <svg class="play" width="58" height="58" viewBox="0 0 58 58"><circle cx="29" cy="29" r="29" fill="#fff"/><path d="M23 18 L40 29 L23 40 Z" fill="#111"/></svg>
  </div>
</section>

<section>
  <div class="control-band"></div>
  <h2 class="control-title">Aesthetic control: how to control it?</h2>

  <div class="card" style="left:112px;top:1395px">
    <svg width="50" height="50" viewBox="0 0 50 50" fill="none" stroke="#0b6fba" stroke-width="2"><rect x="8" y="10" width="30" height="24" rx="2"/><circle cx="23" cy="22" r="5"/><path d="M23 34v6M16 44h14"/><circle cx="42" cy="8" r="4"/><circle cx="6" cy="42" r="4"/></svg>
    <p>Adopting a simple &amp; unambiguous language for a common understanding of aesthetic quality at the extended enterprise level.</p>
  </div>
  <div class="card" style="left:446px;top:1395px">
    <svg width="50" height="50" viewBox="0 0 50 50" fill="none" stroke="#0b6fba" stroke-width="2"><rect x="6" y="30" width="7" height="12"/><rect x="16" y="22" width="7" height="20"/><rect x="26" y="14" width="7" height="28"/><rect x="36" y="6" width="7" height="36"/><path d="M3 46h44"/></svg>
    <p>By using a semantic reference matrix associating the types of anomalies (scratches, marks, deformations, stains, etc.)</p>
  </div>
  <div class="card" style="left:780px;top:1395px">
    <svg width="50" height="50" viewBox="0 0 50 50" fill="none" stroke="#0b6fba" stroke-width="2"><circle cx="20" cy="28" r="9"/><circle cx="20" cy="28" r="3"/><circle cx="35" cy="14" r="7"/><circle cx="35" cy="14" r="2"/><circle cx="37" cy="36" r="6"/><path d="M20 15v4M20 37v4M7 28h4M29 28h4"/></svg>
    <p>Determining the compliance thresholds of the component or product.</p>
  </div>
  <div class="card" style="left:112px;top:1652px">
    <svg width="50" height="50" viewBox="0 0 50 50" fill="none" stroke="#0b6fba" stroke-width="2"><path d="M6 16 L25 8 L44 16 L25 24 Z"/><rect x="9" y="22" width="32" height="20" rx="2"/><path d="M4 44h42"/><path d="M18 34 l5 4 9-9"/></svg>
    <p>Providing uniform training in operational competence for those responsible for aesthetic control.</p>
  </div>
  <div class="card" style="left:446px;top:1652px">
    <svg width="50" height="50" viewBox="0 0 50 50" fill="none" stroke="#0b6fba" stroke-width="2"><path d="M25 4l4 5 6-2 1 6 6 2-2 6 5 4-5 4 2 6-6 2-1 6-6-2-4 5-4-5-6 2-1-6-6-2 2-6-5-4 5-4-2-6 6-2 1-6 6 2z"/><circle cx="25" cy="25" r="10"/><path d="M20 25l4 4 7-7"/></svg>
    <p>By designing realistic and attractive teaching sequences for total quality control.</p>
  </div>
  <div class="card" style="left:780px;top:1652px">
    <svg width="50" height="50" viewBox="0 0 50 50" fill="none" stroke="#0b6fba" stroke-width="2"><circle cx="12" cy="10" r="5"/><circle cx="25" cy="10" r="5"/><circle cx="38" cy="10" r="5"/><path d="M6 44c0-12 8-18 19-18s19 6 19 18"/><circle cx="25" cy="34" r="4"/></svg>
    <p>By regularly assessing the competence to measure the aesthetics, expressed in a tangible, reliable and sustainable way</p>
  </div>
</section>

<section>
  <div class="blob blob-left" style="left:70px;top:2307px;width:153px;height:156px"></div>
  <div class="framed" style="left:112px;top:1985px;width:463px;height:439px">
    <div class="fill" role="img" aria-label="Watchmaker with loupe glasses working on a gold movement" style="background:linear-gradient(135deg,#2c2823,#6b5a45 50%,#1b1815)"></div>
  </div>
  <h2 class="abs section-title feature-title" style="left:633px;top:2050px">Lighten the<br>management of<br>physical components</h2>
  <p class="abs body-copy feature-copy" style="left:635px;top:2196px">Companies must manage and maintain sets of physical components used as a "yardstick" for the training of aesthetic testers. The cost of managing a set of physical parts representing all combinations of shapes, defect types, materials and finishes is very high. KFS allows the company to significantly reduce its management burden by scanning components or products in 3D and then virtually adding 'typical' aesthetic anomalies.</p>
</section>

<section>
  <h2 class="abs section-title feature-title" style="left:112px;top:2610px">Raising awareness of<br>criteria &amp; aesthetic<br>vocabulary</h2>
  <p class="abs body-copy feature-copy" style="left:115px;top:2757px">Aesthetic defects are often the result of careless handling of the components and products concerned, whether during manufacture, assembly or marketing. By making the KFS platform available to staff in direct contact with the product, it becomes very easy to make them aware of the evaluation criteria and the aesthetic vocabulary defined by the company.</p>
  <div class="blob blob-right" style="left:978px;top:2855px;width:154px;height:154px"></div>
  <div class="framed" style="left:624px;top:2532px;width:464px;height:438px">
    <div class="fill" role="img" aria-label="Close-up of tweezers placing a part into an open gold watch movement" style="background:radial-gradient(circle at 50% 55%,#a88a4a,#4a3f2e 45%,#222 80%)"></div>
  </div>
</section>

<section>
  <div class="allows-shape" role="img" aria-label="Blue band with faint watch gears in the background"></div>
  <h2 class="allows-title">KFS ALLOWS</h2>
  <div class="allows-core"><span class="brand-mark"></span>Kestrel Finish<br>Studio</div>

  <div class="node" style="left:481px;top:3265px"><svg width="28" height="28" viewBox="0 0 28 28" fill="none" stroke="#0b6fba" stroke-width="2"><circle cx="14" cy="9" r="5"/><path d="M4 24c2-6 18-6 20 0"/></svg></div>
  <div class="node" style="left:696px;top:3265px"><svg width="28" height="28" viewBox="0 0 28 28" fill="none" stroke="#0b6fba" stroke-width="2"><circle cx="14" cy="14" r="6"/><circle cx="14" cy="14" r="2"/><path d="M14 3v4M14 21v4M3 14h4M21 14h4"/></svg></div>
  <div class="node" style="left:481px;top:3411px"><svg width="28" height="28" viewBox="0 0 28 28" fill="none" stroke="#0b6fba" stroke-width="2"><rect x="4" y="6" width="20" height="14" rx="2"/><path d="M10 24h8"/></svg></div>
  <div class="node" style="left:696px;top:3411px"><svg width="28" height="28" viewBox="0 0 28 28" fill="none" stroke="#0b6fba" stroke-width="2"><circle cx="10" cy="16" r="6"/><circle cx="20" cy="9" r="4"/><circle cx="10" cy="16" r="2"/></svg></div>

  <p class="allows-text left" style="left:195px;top:3266px">Remove the management of components used as standards for aesthetic control training.</p>
  <p class="allows-text left" style="left:195px;top:3411px">To make employees aware of aesthetic control and the vocabulary to be used</p>
  <p class="allows-text" style="left:774px;top:3266px;width:320px">Provide the after-sales service with an efficient tool to record the aesthetic aspect of the supported product</p>
  <p class="allows-text" style="left:774px;top:3411px;width:320px">Integrate aesthetic control into a total quality management (TQM) approach with precise indicators at all stages of the manufacturing and after-sales processes</p>
</section>

<section>
  <div class="blob blob-left" style="left:70px;top:3985px;width:153px;height:152px"></div>
  <div class="framed" style="left:112px;top:3662px;width:463px;height:436px">
    <div class="fill" role="img" aria-label="Hands holding a small watch movement over a green workbench" style="background:linear-gradient(160deg,#5a1d18,#2b2a26 45%,#1d3a34)"></div>
  </div>
  <div class="acc-open">
    <h3><span>IMPROVE AFTER-SALES SERVICCE RETURNS</span><span>-</span></h3>
    <p>The KFS platform can easily be used by the service network staff to assist them in the objective assessment of aesthetic defects by referring to the semantic matrix as well as to the cases already referenced.</p>
  </div>
  <div class="acc-bar" style="top:3936px"><span>IMPROVING THE TOTAL QUALITY</span><span>+</span></div>
  <div class="acc-bar" style="top:3999px"><span>ASESMETIC MATRIX OF AESTHETIC DEFECTS</span><span>+</span></div>
</section>

<footer class="site-footer">
  <div class="footer-col" style="left:118px">
    <h4>Quick Links</h4>
    <ul><li>Home</li><li>Partners</li><li>References</li><li>Info</li><li>Contact Us</li></ul>
  </div>
  <div class="footer-col" style="left:246px;top:99px">
    <ul><li>About Us</li><li>Services</li><li>Testimonials</li><li>Sitemap</li><li>Get A Quote</li></ul>
  </div>
  <div class="footer-col" style="left:401px">
    <h4>Help Links</h4>
    <ul><li>Offers</li><li>Our Blogs</li><li>Privacy Policy</li><li>Terms Of Use</li><li>Help</li></ul>
  </div>
  <div class="footer-col contact" style="left:617px">
    <h4>Reach Us On</h4>
    <ul>
      <li><span class="ico"><svg width="12" height="14" viewBox="0 0 12 14"><path d="M6 0a5 5 0 0 0-5 5c0 4 5 9 5 9s5-5 5-9a5 5 0 0 0-5-5z" fill="#3a8fd6"/><circle cx="6" cy="5" r="2" fill="#1d2234"/></svg></span>Rue des Tilleuls 14 1204 Geneva</li>
      <li><span class="ico"><svg width="12" height="12" viewBox="0 0 12 12"><path d="M2 0l3 3-1.5 1.5a7 7 0 0 0 4 4L9 7l3 3-2 2C5 12 0 7 0 2z" fill="#3a8fd6"/></svg></span>+41 790 555 01 27</li>
      <li><span class="ico"></span>+41 79 555 48 62</li>
      <li><span class="ico"><svg width="13" height="10" viewBox="0 0 13 10"><rect width="13" height="10" rx="1" fill="#3a8fd6"/><path d="M0 1l6.5 5L13 1" stroke="#1d2234" fill="none"/></svg></span>l.ferrand@morvint-works.ch</li>
      <li><span class="ico"></span>m.odier@quillworks.ch</li>
    </ul>
  </div>
  <div class="footer-col" style="left:944px">
    <h4>Follow Us</h4>
    <ul><li>Feedhall</li><li>Snapgrid</li><li>Chirpline</li><li>Workweave</li></ul>
  </div>
  <p class="copyright">Copyright © 2023 Kestrel Finish Studio | All Rights Reserved</p>
</footer>

</body>
</html>
```